Website for Excavator and Earthworks Company

We require a modern, sleek and practical website for our newly created earthworks/excavator business in Perth, Western Australia called Bluegum Ridge Earthworks.

The website should have a modern, cutting edge feel but only needs to be relatively simplistic in it's layout and eventual functionality.

Some pages it should have would be Home, About, Projects and Contact Us.

```html
<!DOCTYPE html>
<html lang="en">
<head>
<meta charset="utf-8">
<title>Bluegum Ridge Earthworks</title>
<link rel="stylesheet" href="https://fonts.googleapis.com/css2?family=Saira+Condensed:wght@600;700;800&family=Barlow:ital,wght@0,400;0,500;0,600;1,500&display=swap">
<style>
:root{
  --lime:#c8dc00;
  --ink:#0d0d0d;
  --dark:#161616;
  --white:#ffffff;
  --grey:#e6e6e6;
  --text:#1c1c1c;
}
*{box-sizing:border-box;margin:0;padding:0}
html,body{width:1200px;height:3236px;overflow:hidden}
body{position:relative;background:var(--white);font-family:'Barlow',sans-serif;color:var(--text)}
.abs{position:absolute}
.display{font-family:'Saira Condensed',sans-serif;font-weight:700;text-transform:uppercase;line-height:1}

/* header */
.site-header{left:0;top:0;width:1200px;height:75px;background:var(--ink)}
.brand{left:112px;top:18px;display:flex;align-items:center;gap:8px}
.brand-dot{width:14px;height:14px;background:var(--lime)}
.brand-name{font-family:'Saira Condensed',sans-serif;font-weight:700;font-size:17px;color:var(--white);text-transform:uppercase;line-height:1.05;width:120px}
.main-nav{left:416px;top:32px;display:flex;gap:30px}
.main-nav a{font-family:'Saira Condensed',sans-serif;font-weight:700;font-size:12px;color:var(--white);text-decoration:none;text-transform:uppercase;letter-spacing:.3px}
.main-nav a.active{color:var(--lime);border-bottom:2px solid var(--lime);padding-bottom:3px}
.header-phone{left:743px;top:25px;display:flex;align-items:center;gap:9px;font-family:'Saira Condensed',sans-serif;font-weight:700;font-size:21px;color:var(--white);letter-spacing:.5px}
.icon-circle{width:26px;height:26px;border-radius:50%;background:#3a3a3a;display:flex;align-items:center;justify-content:center}
.btn-header{left:950px;top:21px;width:138px;height:34px;background:var(--lime);clip-path:polygon(0 0,88% 0,100% 100%,0 100%);font-family:'Saira Condensed',sans-serif;font-weight:700;font-size:12px;text-transform:uppercase;display:flex;align-items:center;padding-left:28px;color:var(--ink)}

/* hero */
.hero{left:0;top:75px;width:1200px;height:590px;overflow:hidden;background:linear-gradient(180deg,#3c4a3c 0%,#25301f 45%,#1b1b1a 100%)}
.hero-machine{left:520px;top:70px;width:600px;height:540px;background:radial-gradient(ellipse at 55% 50%,#c9b333 0%,#6f6a33 45%,rgba(40,40,30,0) 72%)}
.hero-eyebrow{left:112px;top:97px;font-family:'Saira Condensed',sans-serif;font-weight:700;font-size:15px;color:var(--white);text-transform:uppercase;display:flex;align-items:center;gap:6px}
.hero-eyebrow span{display:inline-block;width:50px;height:3px;background:var(--lime)}
.hero-title{left:110px;top:128px;font-size:74px;color:var(--white);line-height:.98}
.hero-title em{font-style:normal;color:var(--lime)}
.hero-text{left:112px;top:424px;width:310px;font-size:12.5px;line-height:1.5;color:var(--white)}
.play{left:931px;top:462px;display:flex;align-items:center;gap:14px}
.play-btn{width:68px;height:68px;border-radius:50%;border:4px solid #8a8a78;display:flex;align-items:center;justify-content:center}
.play-label{font-style:italic;font-weight:500;font-size:22px;color:var(--white)}
.corner-grey{left:1045px;top:640px}

/* services */
.eyebrow{font-size:10px;font-weight:500;text-transform:uppercase;display:flex;align-items:center;gap:6px;color:var(--text)}
.eyebrow i{display:inline-block;width:45px;height:2px;background:var(--ink)}
.section-title{font-size:40px;color:var(--ink);text-align:center;width:1200px;left:0}
.services-eyebrow{left:0;width:1200px;top:720px;justify-content:center}
.services-title{top:738px}
.service-card{top:803px;width:314px;height:319px;overflow:hidden}
.service-card .photo{width:100%;height:100%}
.service-card .shade{left:0;bottom:0;width:100%;height:130px;background:linear-gradient(180deg,rgba(0,0,0,0) 0%,rgba(0,0,0,.85) 100%)}
.service-card h3{left:24px;bottom:18px;font-size:20px;color:var(--white);line-height:1.2}
.service-card .corner{right:0;bottom:0;width:68px;height:68px;background:var(--lime);clip-path:polygon(100% 0,100% 100%,0 100%)}
.service-card .go{right:14px;bottom:10px;width:24px;height:24px;border-radius:50%;background:var(--white);display:flex;align-items:center;justify-content:center}
.green-wedge{left:0;top:1053px}

/* about */
.about{left:0;top:1186px;width:1200px;height:509px;background:var(--lime)}
.about-photo{left:547px;top:0;width:653px;height:509px;background:linear-gradient(160deg,#b8a97a 0%,#8a8a84 40%,#c9cbcf 75%,#e2e3e6 100%)}
.about-eyebrow{left:112px;top:91px}
.about-eyebrow i{width:55px;height:1px;background:#6a7400}
.about-title{left:112px;top:116px;font-size:38px;line-height:1.19;color:var(--ink)}
.about-text{left:112px;top:260px;width:395px;font-size:11.5px;line-height:1.5;color:var(--ink)}
.btn-dark{background:var(--ink);color:var(--white);font-family:'Saira Condensed',sans-serif;font-weight:700;font-size:12px;text-transform:uppercase;display:flex;align-items:center;justify-content:center;clip-path:polygon(0 0,88% 0,100% 100%,8% 100%)}
.about-btn{left:112px;top:354px;width:226px;height:42px}

/* projects */
.projects-eyebrow{left:0;width:1200px;top:1736px;justify-content:center}
.projects-title{top:1755px}
.project{width:366px;height:243px}
.project .tag{left:0;top:0;background:var(--ink);color:var(--white);font-family:'Saira Condensed',sans-serif;font-weight:700;font-size:11px;padding:3px 18px 3px 20px;clip-path:polygon(0 0,100% 0,92% 100%,0 100%)}
.btn-lime{left:499px;top:2350px;width:202px;height:40px;background:var(--lime);clip-path:polygon(0 0,88% 0,100% 100%,12% 100%);font-family:'Saira Condensed',sans-serif;font-weight:700;font-size:12px;text-transform:uppercase;display:flex;align-items:center;justify-content:center;color:var(--ink)}

/* contact */
.contact-green{left:594px;top:2447px;width:606px;height:553px;background:var(--lime)}
.contact-wedge{left:1080px;top:2327px}
.ghost-word{left:-10px;top:2452px;font-size:190px;color:#ededed;letter-spacing:2px;white-space:nowrap;font-weight:800}
.contact-photo{left:0;top:2582px;width:660px;height:418px;background:linear-gradient(110deg,#c9c8b8 0%,#9aa0a2 45%,#b26b4c 70%,#8d8f90 100%)}
.contact-title{right:112px;top:2503px;font-size:36px;line-height:1.27;color:var(--ink);text-align:right}
.field{left:721px;width:367px;height:33px;border:1px solid #4e5600;font-size:11px;color:#3a3f00;padding:9px 13px}
.field.tall{height:87px}
.submit{left:721px;top:2906px;width:366px;height:39px;background:var(--ink);color:var(--white);clip-path:polygon(0 0,97% 0,100% 100%,7% 100%);display:flex;align-items:center;justify-content:center;font-family:'Saira Condensed',sans-serif;font-weight:700;font-size:13px;text-transform:uppercase}

/* footer */
.site-footer{left:0;top:3000px;width:1200px;height:236px;background:var(--ink);color:var(--white)}
.footer-brand{left:112px;top:40px}
.footer-about{left:112px;top:110px;width:200px;font-size:8.5px;line-height:1.75;color:#d8d8d8}
.footer-col h4{font-family:'Saira Condensed',sans-serif;font-weight:700;font-size:14px;text-transform:uppercase;letter-spacing:.4px}
.footer-col h4::after{content:"";display:block;width:28px;height:2px;background:var(--lime);margin-top:5px}
.footer-col ul{list-style:none;margin-top:14px}
.footer-col li{font-size:8.5px;line-height:17.6px;color:#dcdcdc;display:flex;align-items:center;gap:8px}
.footer-col li.icon{line-height:26px}
.dot{width:18px;height:18px;border-radius:50%;background:var(--white);display:inline-block}
.vline{top:40px;width:1px;height:145px;background:#2e2e2e}
.footer-rule{left:112px;top:190px;width:976px;height:1px;background:#2e2e2e}
.copyright{left:112px;top:208px;font-size:8px;color:#cfcfcf}
.legal{right:112px;top:208px;font-size:8px;color:#cfcfcf;display:flex;gap:8px}
</style>
</head>
<body>

<header class="site-header abs">
  <div class="brand abs"><span class="brand-dot"></span><span class="brand-name">Bluegum Ridge<br>Earthworks</span></div>
  <nav class="main-nav abs">
    <a class="active" href="#">Home</a><a href="#">About Us</a><a href="#">Projects</a><a href="#">Contact Us</a>
  </nav>
  <div class="header-phone abs">
    <span class="icon-circle"><svg width="13" height="13" viewBox="0 0 24 24"><path fill="#d4d4d4" d="M6.6 10.8a15.1 15.1 0 0 0 6.6 6.6l2.2-2.2c.3-.3.7-.4 1-.2 1.1.4 2.3.6 3.6.6.6 0 1 .4 1 1V20c0 .6-.4 1-1 1C10.6 21 3 13.4 3 4c0-.6.4-1 1-1h3.5c.6 0 1 .4 1 1 0 1.3.2 2.5.6 3.6.1.3 0 .7-.2 1z"/></svg></span>
    +61 400 318 562
  </div>
  <div class="btn-header abs">Contact Us</div>
</header>

<section class="hero abs">
  <svg class="abs" style="left:0;top:0" width="1200" height="590">
    <polygon points="305,0 1200,0 1200,150 1030,320 760,590 650,590 650,470 460,470 460,300 305,300" fill="#5a6a12" opacity=".55"/>
    <polygon points="700,0 1020,0 1200,180 1200,300 1020,120 860,120" fill="#8ba21a" opacity=".45"/>
  </svg>
  <div class="hero-machine abs" role="img" aria-label="Yellow mini excavator with raised arm against a green field"></div>
  <div class="hero-eyebrow abs">Welcome to Bluegum Ridge Earthworks. <span></span></div>
  <h1 class="hero-title display abs">Precision<br>Earthworks,<br>Powered by<br><em>Experience</em></h1>
  <p class="hero-text abs">Bluegum Ridge Earthworks delivers expert excavation and site preparation services across Perth and Western Australia, combining cutting-edge machinery with trusted workmanship.</p>
  <div class="play abs">
    <div class="play-btn"><svg width="22" height="24" viewBox="0 0 22 24"><polygon points="2,1 21,12 2,23" fill="#c8dc00"/></svg></div>
    <span class="play-label">Play Now</span>
  </div>
</section>
<svg class="corner-grey abs" width="155" height="150"><polygon points="20,0 155,0 155,150" fill="#ececec"/><polygon points="0,0 40,0 60,45" fill="#d8d8d8"/></svg>

<div class="eyebrow services-eyebrow abs"><i></i>Services<i></i></div>
<h2 class="section-title display abs services-title">Bluegum Ridge Earthworks Services</h2>

<svg class="green-wedge abs" width="140" height="135"><polygon points="0,0 135,133 0,133" fill="#c8dc00"/></svg>

<article class="service-card abs" style="left:112px">
  <div class="photo" role="img" aria-label="Residential building frame under construction with excavator on site" style="background:linear-gradient(180deg,#9fb8c9 0%,#7d8a6a 40%,#6b5a47 75%,#3d3128 100%)"></div>
  <div class="shade abs"></div>
  <h3 class="display abs">Civil &amp; Residential<br>Earthworks</h3>
  <div class="corner abs"></div>
  <div class="go abs"><svg width="12" height="12" viewBox="0 0 12 12"><path d="M1 6h9M7 3l3 3-3 3" stroke="#111" stroke-width="1.3" fill="none"/></svg></div>
</article>
<article class="service-card abs" style="left:442px">
  <div class="photo" role="img" aria-label="Orange excavators levelling a wide dirt site" style="background:linear-gradient(180deg,#b9c9d6 0%,#a99d82 35%,#9a7552 65%,#4a3626 100%)"></div>
  <div class="shade abs"></div>
  <h3 class="display abs">Land Levelling<br>&amp; Preparation</h3>
  <div class="corner abs"></div>
  <div class="go abs"><svg width="12" height="12" viewBox="0 0 12 12"><path d="M1 6h9M7 3l3 3-3 3" stroke="#111" stroke-width="1.3" fill="none"/></svg></div>
</article>
<article class="service-card abs" style="left:773px">
  <div class="photo" role="img" aria-label="Cleared quarry cliff edge with green bushland above" style="background:linear-gradient(180deg,#a9c3d8 0%,#4f7a3a 30%,#7b6a55 60%,#3a302a 100%)"></div>
  <div class="shade abs"></div>
  <h3 class="display abs">Bulk Excavation &amp;<br>Site Clearing</h3>
  <div class="corner abs"></div>
  <div class="go abs"><svg width="12" height="12" viewBox="0 0 12 12"><path d="M1 6h9M7 3l3 3-3 3" stroke="#111" stroke-width="1.3" fill="none"/></svg></div>
</article>

<section class="about abs">
  <div class="about-photo abs" role="img" aria-label="Worker in hard hat and hi-vis vest standing in the cab of a dump truck"></div>
  <svg class="abs" style="left:547px;top:0" width="340" height="509"><polygon points="0,0 0,240 120,240 0,509 50,509 180,290 40,240" fill="#c8dc00" opacity="0"/><polygon points="0,240 160,240 160,260 0,260" fill="#c8dc00"/><polygon points="0,0 0,240 40,240 0,0" fill="#c8dc00" opacity="0"/></svg>
  <div class="eyebrow about-eyebrow abs">About Us<i></i></div>
  <h2 class="about-title display abs">Mini Excavator<br>and Earthworks for<br>Perth and Surrounds</h2>
  <p class="about-text abs">With years of experience in earthworks and site preparation, Bluegum Ridge Earthworks is committed to delivering safe, efficient, and reliable services for residential, commercial, and civil projects. Our skilled team and modern fleet ensure every job is completed on time and to the highest standard.</p>
  <div class="btn-dark about-btn abs">Learn More About Us</div>
</section>

<div class="eyebrow projects-eyebrow abs"><i></i>Projects<i></i></div>
<h2 class="section-title display abs projects-title">Our Recent Projects</h2>

<div class="project abs" style="left:36px;top:1818px"><div role="img" aria-label="Excavators digging a large foundation pit" style="width:100%;height:100%;background:linear-gradient(180deg,#a9bccb 0%,#8d7a62 40%,#7a5f45 100%)"></div><span class="tag abs">Project 1</span></div>
<div class="project abs" style="left:417px;top:1818px"><div role="img" aria-label="Cleared forest land with tree stumps" style="width:100%;height:100%;background:linear-gradient(180deg,#5c6e4c 0%,#6b5a40 45%,#5a4632 100%)"></div><span class="tag abs">Project 2</span></div>
<div class="project abs" style="left:798px;top:1818px"><div role="img" aria-label="Aerial view of an orange excavator on rocky ground" style="width:100%;height:100%;background:linear-gradient(135deg,#8b7760 0%,#6c6459 50%,#9a8468 100%)"></div><span class="tag abs">Project 3</span></div>
<div class="project abs" style="left:36px;top:2076px"><div role="img" aria-label="City excavation site beside high-rise buildings" style="width:100%;height:100%;background:linear-gradient(180deg,#b7c4cc 0%,#8e9aa1 35%,#9b6b4a 70%,#6e5038 100%)"></div><span class="tag abs">Project 4</span></div>
<div class="project abs" style="left:417px;top:2076px"><div role="img" aria-label="Excavated quarry with bushland on the ridge" style="width:100%;height:100%;background:linear-gradient(180deg,#a9c3d8 0%,#4f7a3a 30%,#9b7d66 65%,#8a6c58 100%)"></div><span class="tag abs">Project 5</span></div>
<div class="project abs" style="left:798px;top:2076px"><div role="img" aria-label="Excavator working on a riverside construction site" style="width:100%;height:100%;background:linear-gradient(180deg,#a9a49a 0%,#7d776c 40%,#b66a45 70%,#6a5a4a 100%)"></div><span class="tag abs">Project 6</span></div>

<div class="btn-lime abs">View All Projects</div>

<svg class="contact-wedge abs" width="120" height="121"><polygon points="120,0 120,121 0,121" fill="#c8dc00"/></svg>
<div class="contact-green abs"></div>
<div class="ghost-word display abs">Bluegum</div>
<div class="contact-photo abs" role="img" aria-label="Site manager in hard hat talking on the phone with plans, roller in background"></div>

<h2 class="contact-title display abs">Ready to start your<br>project? Contact us<br>today for a free quote.</h2>
<div class="field abs" style="top:2659px">Your Name Here*</div>
<div class="field abs" style="top:2702px">Your Email Here*</div>
<div class="field abs" style="top:2744px">Your Mobile Here*</div>
<div class="field tall abs" style="top:2787px">Your Subject Here*</div>
<div class="submit abs">Submit</div>

<footer class="site-footer abs">
  <div class="brand footer-brand abs"><span class="brand-dot"></span><span class="brand-name">Bluegum Ridge<br>Earthworks</span></div>
  <p class="footer-about abs">With years of experience in earthworks and site preparation, Bluegum Ridge Earthworks is committed to delivering safe, efficient, and reliable services for residential, commercial, and civil projects.</p>
  <div class="vline abs" style="left:364px"></div>
  <div class="footer-col abs" style="left:453px;top:42px"><h4>Quick Links</h4><ul><li>Home</li><li>About Us</li><li>Projects</li><li>Contact Us</li></ul></div>
  <div class="vline abs" style="left:620px"></div>
  <div class="footer-col abs" style="left:679px;top:42px"><h4>Contact Us</h4><ul>
    <li class="icon"><span class="dot"></span>+61 400 318 562</li>
    <li class="icon" style="color:var(--lime)"><span class="dot"></span>info@bluegumridgeworks.com.au</li></ul></div>
  <div class="vline abs" style="left:891px"></div>
  <div class="footer-col abs" style="left:966px;top:42px"><h4>Follow Us</h4><ul>
    <li class="icon"><span class="dot"></span>Community</li>
    <li class="icon"><span class="dot"></span>Network</li>
    <li class="icon"><span class="dot"></span>Videos</li></ul></div>
  <div class="footer-rule abs"></div>
  <p class="copyright abs">Copyright © Bluegum Ridge Earthworks. 2026 All Rights Reserved</p>
  <p class="legal abs"><span>Privacy Policy</span><span>Terms and Conditions</span></p>
</footer>

</body>
</html>
```